Brindlewood Elementary School 2019-2020 Priority Goals

This visual will encapsulate our school's annual goals. We are a large elementary school in a high performing school district. We base our annual goals primarily on our school generated set of foundational promises. We know that the relationships of the people are critical to our success. The product will primarily be used with our staff internally to keep focused on our priority goals for the year, which are to innovate and collaborate. The collaboration is both amongst staff and also in stronger partnerships with our parent community. The innovation is in not settling for how things have always been done and will focus in three areas: future ready skills, academic growth and achievement and finally in social/emotional growth. We have been saying to one another that "we will accelerate the academic and social emotional growth of the students we serve by innovating and collaborating.

Target Market(s)

Staff, parents and school board

Industry/Entity Type

Education

Font styles to use
Other font styles liked:
• open to your ideas

Colors
0255a3
fbed22

Requirements
Must have
• pretty new to this idea, we'll attach the early sketches below. You'll also find a school logo design as well as the promises that are referred to in the sketch.
Nice to have
• the colors below are school colors, but we are open to your creative genius as well.

```html
<!DOCTYPE html>
<html lang="en">
<head>
<meta charset="utf-8">
<title>Brindlewood Elementary School – Foundation Beliefs &amp; Promises</title>
<link rel="stylesheet" href="https://fonts.googleapis.com/css2?family=Archivo:wght@400;500&family=Mulish:wght@400&family=Roboto+Condensed:wght@700&display=swap">
<style>
  :root {
    --school-blue: #0255a3;
    --school-yellow: #fbed22;
    --heart-yellow: #f9ea26;
    --paper: #ffffff;
  }
  html, body {
    margin: 0;
    padding: 0;
    overflow: hidden;
    background: var(--paper);
  }
  .poster {
    position: relative;
    width: 1200px;
    height: 1200px;
    background: var(--paper);
    overflow: hidden;
  }
  .school-mark {
    position: absolute;
    left: 14px;
    top: 40px;
    width: 220px;
    display: flex;
    flex-direction: column;
    align-items: flex-start;
    gap: 12px;
  }
  .school-mark__dot {
    width: 64px;
    height: 64px;
    border-radius: 50%;
    background: var(--school-yellow);
  }
  .school-mark__name {
    font-family: "Roboto Condensed", "Arial Narrow", sans-serif;
    font-weight: 700;
    font-size: 30px;
    line-height: 1.05;
    color: var(--school-blue);
    text-transform: uppercase;
  }
  .poster-title {
    position: absolute;
    left: 266px;
    top: 88px;
    margin: 0;
    font-family: "Mulish", "Avenir", sans-serif;
    font-weight: 400;
    font-size: 63px;
    letter-spacing: -0.5px;
    color: var(--school-blue);
    white-space: nowrap;
  }
  .heart-art {
    position: absolute;
    left: 0;
    top: 0;
    width: 1200px;
    height: 1200px;
  }
  .heart-fill { fill: var(--heart-yellow); }
  .heart-outline {
    fill: none;
    stroke: var(--school-blue);
    stroke-width: 5;
    stroke-linecap: round;
  }
  .promise-label {
    font-family: "Archivo", sans-serif;
    font-weight: 400;
    font-size: 20px;
    letter-spacing: 0.6px;
  }
  .promise-label--ink { fill: var(--school-blue); }
  .promise-label--knockout {
    fill: #000;
    stroke: #000;
    stroke-width: 18px;
    stroke-linejoin: round;
  }
  .goal-text {
    font-family: "Roboto Condensed", "Arial Narrow", sans-serif;
    font-weight: 700;
    fill: var(--school-blue);
  }
  .goal-text--statement { font-size: 34px; }
  .goal-text--pillar { font-size: 39px; }
  .goal-text--detail { font-size: 26px; }
  .goal-text--leaf { font-size: 25px; }
  .branch {
    stroke: var(--school-blue);
    stroke-width: 1.6;
    fill: none;
  }
</style>
</head>
<body>
<main class="poster">
  <div class="school-mark">
    <span class="school-mark__dot"></span>
    <span class="school-mark__name">Brindlewood Elementary School</span>
  </div>

  <h1 class="poster-title">Foundation Believe &amp; Promises</h1>

  <svg class="heart-art" viewBox="0 0 1200 1200" xmlns="http://www.w3.org/2000/svg">
    <defs>
      <path id="guide-top-left" d="M140 580 C120 440 170 310 300 260 C420 215 560 260 632 368"/>
      <path id="guide-top-right" d="M632 368 C700 270 840 225 960 262 C1080 300 1140 430 1132 560"/>
      <path id="guide-left-side" d="M140 580 C160 720 280 850 400 960 C500 1060 590 1140 632 1178"/>
      <path id="guide-right-side" d="M632 1178 C680 1135 770 1060 870 960 C1000 830 1120 720 1132 560"/>

      <mask id="label-gaps" maskUnits="userSpaceOnUse" x="0" y="0" width="1200" height="1200">
        <rect x="0" y="0" width="1200" height="1200" fill="#fff"/>
        <g class="promise-label promise-label--knockout" dominant-baseline="central">
          <text><textPath href="#guide-top-left" startOffset="64%" text-anchor="middle">Relationships</textPath></text>
          <text><textPath href="#guide-top-right" startOffset="46%" text-anchor="middle">Listen ! Every student has a song</textPath></text>
          <text><textPath href="#guide-left-side" startOffset="12%" text-anchor="middle">Marla Finch</textPath></text>
          <text><textPath href="#guide-left-side" startOffset="62%" text-anchor="middle">Listening for student's song</textPath></text>
          <text><textPath href="#guide-right-side" startOffset="34%" text-anchor="middle">Marla Finch</textPath></text>
          <text><textPath href="#guide-right-side" startOffset="84%" text-anchor="middle">Relationships</textPath></text>
        </g>
      </mask>
    </defs>

    <path class="heart-fill" d="M632 420 C560 300 430 255 330 280 C205 315 155 440 168 560 C185 700 300 830 420 950 C520 1050 600 1115 632 1140 C670 1110 760 1040 860 950 C990 830 1090 700 1102 560 C1112 430 1045 310 920 280 C800 255 690 320 632 420 Z"/>

    <path class="heart-outline" mask="url(#label-gaps)" d="M632 368 C560 260 420 215 300 260 C170 310 120 440 140 580 C160 720 280 850 400 960 C500 1060 590 1140 632 1178 C680 1135 770 1060 870 960 C1000 830 1120 720 1132 560 C1140 430 1080 300 960 262 C840 225 700 270 632 368 Z"/>

    <g class="promise-label promise-label--ink" dominant-baseline="central">
      <text><textPath href="#guide-top-left" startOffset="64%" text-anchor="middle">Relationships</textPath></text>
      <text><textPath href="#guide-top-right" startOffset="46%" text-anchor="middle">Listen ! Every student has a song</textPath></text>
      <text><textPath href="#guide-left-side" startOffset="12%" text-anchor="middle">Marla Finch</textPath></text>
      <text><textPath href="#guide-left-side" startOffset="62%" text-anchor="middle">Listening for student's song</textPath></text>
      <text><textPath href="#guide-right-side" startOffset="34%" text-anchor="middle">Marla Finch</textPath></text>
      <text><textPath href="#guide-right-side" startOffset="84%" text-anchor="middle">Relationships</textPath></text>
    </g>

    <g class="goal-text goal-text--statement" text-anchor="middle">
      <text x="632" y="464">We will accelerate the</text>
      <text x="632" y="508">academic &amp; social/emotional growth</text>
      <text x="632" y="551">of the students we serve by :</text>
    </g>

    <g class="goal-text goal-text--pillar" text-anchor="middle">
      <text x="402" y="648">Innovating</text>
      <text x="604" y="648">And</text>
      <text x="813" y="648">Collaborating</text>
    </g>

    <g class="goal-text goal-text--detail" text-anchor="middle">
      <text x="402" y="675">Agents of change</text>
      <text x="402" y="700">Learners</text>
    </g>

    <g class="branch">
      <line x1="316" y1="710" x2="316" y2="730"/>
      <line x1="402" y1="710" x2="402" y2="730"/>
      <line x1="489" y1="710" x2="489" y2="730"/>
      <polyline points="766,698 813,654 858,698"/>
    </g>

    <g class="goal-text goal-text--leaf">
      <text x="316" y="751" text-anchor="middle">Social</text>
      <text x="402" y="751" text-anchor="middle">Future</text>
      <text x="489" y="751" text-anchor="middle">Ready</text>
      <text x="757" y="723" text-anchor="middle">Staff</text>
      <text x="824" y="723">Parent</text>
      <text x="824" y="747">Partnerships</text>
      <text x="802" y="781" text-anchor="middle">Team</text>
      <text x="802" y="805" text-anchor="middle">Players</text>
    </g>
  </svg>
</main>
</body>
</html>
```